Letterhead, stationery and email signature for construction business

I need the letterhead, stationery and email signature designs for a construction business. I want them to have a corporate feel to them.

I've attached the logo for reference.

```html
<!DOCTYPE html>
<html lang="en">
<head>
<meta charset="utf-8">
<title>Bravor Stationery</title>
<link rel="stylesheet" href="https://fonts.googleapis.com/css2?family=Arimo:wght@400;700&family=Hind:wght@600&display=swap">
<style>
  :root {
    --brand-blue: #2f56a5;
    --brand-grey: #55565f;
    --text: #4b4b4f;
    --paper: #ffffff;
    --backdrop: #dcdcdc;
  }
  * { margin: 0; padding: 0; box-sizing: border-box; }
  html, body { width: 891px; height: 1200px; overflow: hidden; }
  body {
    position: relative;
    background: var(--backdrop);
    font-family: "Arimo", Arial, sans-serif;
    color: var(--text);
  }
  .sheet, .card {
    position: absolute;
    left: 109px;
    width: 538px;
    background: var(--paper);
    box-shadow: 2px 3px 5px rgba(0,0,0,.28);
    overflow: hidden;
  }
  .sheet { top: 69px; height: 761px; }
  .card { top: 896px; height: 206px; }
  .abs { position: absolute; }
  .band { position: absolute; background: var(--brand-blue); }
  .rule { position: absolute; background: var(--brand-grey); }
  .brand-mark { position: absolute; background: var(--brand-blue); }
  .brand-name {
    position: absolute;
    font-weight: 700;
    color: var(--brand-blue);
    line-height: 1;
    white-space: nowrap;
  }
  .divider { position: absolute; width: 1px; background: var(--brand-grey); }
  .icon { width: 9px; height: 9px; vertical-align: middle; margin-right: 4px; }
  .icon path, .icon circle, .icon rect { fill: none; stroke: var(--brand-blue); stroke-width: 1.4; }

  /* letterhead header */
  .head-address {
    position: absolute; right: 161px; top: 35px;
    text-align: right; font-size: 9.5px; line-height: 14px;
  }
  .head-contact {
    position: absolute; left: 396px; top: 35px;
    font-size: 9.5px; line-height: 14px;
  }

  /* letter body */
  .letter { position: absolute; left: 48px; top: 234px; width: 450px; }
  .salutation {
    font-family: "Hind", Arial, sans-serif; font-weight: 600;
    font-size: 12px; margin-bottom: 20px; color: #444;
  }
  .letter p {
    font-size: 8.9px; line-height: 11px; margin-bottom: 10px; white-space: nowrap;
  }
  .closing {
    font-family: "Hind", Arial, sans-serif; font-weight: 600;
    font-size: 7px; margin-top: 18px;
  }
  .signature {
    position: absolute; left: 48px; top: 529px; width: 89px; height: 27px;
    background: linear-gradient(90deg, #d9d9dc, #eeeeef);
  }

  /* card */
  .holder-name {
    position: absolute; right: 31px; top: 20px;
    font-size: 20px; font-weight: 700; color: var(--brand-blue);
  }
  .holder-role {
    position: absolute; right: 31px; top: 45px; font-size: 14px;
  }
  .card-contact {
    position: absolute; left: 33px; top: 115px;
    font-size: 14.5px; line-height: 21.5px;
  }
  .card-contact .icon { width: 12px; height: 12px; margin-right: 7px; }
  .card-address {
    position: absolute; left: 247px; top: 136px;
    font-size: 14.5px; line-height: 21.5px;
  }
</style>
</head>
<body>

<section class="sheet" aria-label="Letterhead">
  <div class="band" style="left:0;top:84px;width:42px;height:9px"></div>
  <div class="band" style="left:206px;top:84px;width:332px;height:9px"></div>
  <div class="rule" style="left:0;top:97px;width:47px;height:2px"></div>
  <div class="rule" style="left:85px;top:97px;width:453px;height:2px"></div>
  <div class="brand-mark" style="left:49px;top:62px;width:33px;height:33px"></div>
  <div class="brand-name" style="left:88px;top:64px;font-size:25px">BRAVOR</div>

  <div class="head-address">Your Address<br>City<br>State, Zip 0000</div>
  <div class="divider" style="left:386px;top:37px;height:38px"></div>
  <div class="head-contact">
    <div><svg class="icon" viewBox="0 0 12 12"><path d="M3 1 L5 3.5 L4 5 Q5 7 7 8 L8.5 7 L11 9 L10 11 Q4 11 1 2 Z"/></svg>123-456-2100</div>
    <div><svg class="icon" viewBox="0 0 12 12"><rect x="1" y="2.5" width="10" height="7"/><path d="M1 2.5 L6 7 L11 2.5"/></svg>youremail@gmail.com</div>
    <div><svg class="icon" viewBox="0 0 12 12"><circle cx="6" cy="6" r="5"/><path d="M1 6 H11 M6 1 Q2.5 6 6 11 Q9.5 6 6 1"/></svg>www.yourwebsite.com</div>
  </div>

  <div class="letter">
    <div class="salutation">Dear Mr. Carter,</div>
    <p>Lorem ipsum dolor sit amet, consectetuer adipiscing elit, sed diam nonmmy nibh euismod tincidunt ut laor<br>eet dolore magna aliquam erat volutpat. Ut wisi enim ad minim veniam, quis nostrud exerci tationmcorper<br>suscipit lobortis nisl ut aliquip ex ea commodo consequat. Duis autem vel eum iriure dolor in hendrerit in<br>vulputate velit esse molestie consequat, vel illum dolore eu feugiat</p>
    <p>Rorem ipsum dolor sit amet, consectetuer adipiscing elit, sed diam nonmmy nibh euismod tincidunt ut laor<br>eet dolore magna aliquam erat volutpat. Ut wisi enim ad minim veniam, quis nostrud exerci tationmcorper<br>suscipit lobortis nisl ut aliquip ex ea commodo consequat. Duis autem vel eum iriure dolor in hendrerit in<br>vulputate velit esse molest</p>
    <p>Dorem ipsum dolor sit amet, consectetuer adipiscing elit, sed diam nonmmy nibh euismod tincidunt ut laor<br>eet dolore magna aliquam erat volutpat. Ut wisi enim ad minim veniam, quis nostrud exerci tationmcorper<br>suscipit lobortis nisl ut aliquip ex ea commodo consequat. Duis autem vel eum iriure dolor in hendrerit in<br>suscipit lobortis nisl ut aliquip ex ea commodo consequat. Duis autem vel eum iriure dolor in hendrerit in<br>vulputate velit esse molestie consequat, vel illum</p>
    <p>Sorem ipsum dolor sit amet, consectetuer adipiscing elit, sed diam nonmmy nibh euismod tincidunt ut laor<br>eet dolore magna aliquam erat volutpat. Ut wisi enim ad minim veniam, quis nostrud exerci tationmcorper<br>suscipit lobortis nisl ut aliquip ex ea commodo consequat. Duis autem vel eum iriure dolor in</p>
    <div class="closing">Sincerely,</div>
  </div>
  <div class="signature" role="img" aria-label="Handwritten signature of the sender"></div>
</section>

<section class="card" aria-label="Business card">
  <div class="holder-name">DANIEL HART</div>
  <div class="holder-role">Manager</div>

  <div class="band" style="left:0;top:73px;width:29px;height:12px"></div>
  <div class="band" style="left:281px;top:73px;width:257px;height:12px"></div>
  <div class="rule" style="left:0;top:93px;width:37px;height:2px"></div>
  <div class="rule" style="left:93px;top:93px;width:445px;height:2px"></div>
  <div class="brand-mark" style="left:38px;top:37px;width:52px;height:52px"></div>
  <div class="brand-name" style="left:99px;top:40px;font-size:38px">BRAVOR</div>

  <div class="card-contact">
    <div><svg class="icon" viewBox="0 0 12 12"><path d="M3 1 L5 3.5 L4 5 Q5 7 7 8 L8.5 7 L11 9 L10 11 Q4 11 1 2 Z"/></svg>123-456-2100</div>
    <div><svg class="icon" viewBox="0 0 12 12"><rect x="1" y="2.5" width="10" height="7"/><path d="M1 2.5 L6 7 L11 2.5"/></svg>youremail@gmail.com</div>
    <div><svg class="icon" viewBox="0 0 12 12"><circle cx="6" cy="6" r="5"/><path d="M1 6 H11 M6 1 Q2.5 6 6 11 Q9.5 6 6 1"/></svg>www.yourwebsite.com</div>
  </div>
  <div class="divider" style="left:226px;top:120px;height:59px"></div>
  <div class="card-address">Your Address<br>City, State, Zip 0000</div>
</section>

</body>
</html>
```